Business Card for Multi-Brand Sportswear Company

We are looking for a business card which represents our company and the multiple brands within it.

The company: Fen Athletics (LTD)
The brands: Fen, TavaPuni, ElmStretch, Grit and Rain

Employees using these cards would be representing Fen Athletics, rather than any of the individual brands. You will see a current design within the uploaded files, to give some inspiration. The actual text of the brands is not necessary, but the logos should be on there is some format.

Our creative minds on this are stretched, so we are looking for someone to make this their own, and show us what a good business card should look like.

We may like to get these printed with spot gloss, so keep that in mind with your designs.

www.fenathletics.co.uk

Industry/Entity Type

Business

Contact Information for Business Card

Leo Pemberton-Hale
Operations Manager
(+44) 1632 960 418
Leo@fenathletics.co.uk
www.fenathletics.co.uk

Font styles to use
Sans Serif
Other font styles liked:
• Eurostile

Colors
ffffff

Requirements
Nice to have
• Dark (black) background

```html
<!DOCTYPE html>
<html lang="en">
<head>
<meta charset="utf-8">
<title>Fen Athletics – Business Card</title>
<link rel="stylesheet" href="https://fonts.googleapis.com/css2?family=Saira:wght@400;500;600&display=swap">
<style>
  :root {
    --page: #ececec;
    --card-dark: #2a2a2a;
    --card-dark-deep: #1f1f1f;
    --card-light: #f7f7f7;
    --card-light-shade: #e4e4e4;
    --white: #ffffff;
    --ink: #111111;
    --accent: #e3262b;
    --muted: #8a8a8a;
  }
  * { margin: 0; padding: 0; box-sizing: border-box; }
  html, body { width: 1200px; height: 586px; overflow: hidden; }
  body {
    background: var(--page);
    font-family: "Saira", sans-serif;
    position: relative;
  }
  .card {
    position: absolute;
    top: 129px;
    width: 501px;
    height: 301px;
    overflow: hidden;
  }
  .card--front { left: 65px; }
  .card--back { left: 608px; }

  .facet-texture {
    position: absolute; inset: 0;
  }
  .card--front .facet-texture {
    background: linear-gradient(135deg, var(--card-dark) 0%, var(--card-dark-deep) 45%, var(--card-dark) 70%, var(--card-dark-deep) 100%);
  }
  .card--back .facet-texture {
    background: linear-gradient(135deg, var(--white) 0%, var(--card-light-shade) 35%, var(--card-light) 60%, var(--card-light-shade) 100%);
  }

  /* Front */
  .wordmark {
    position: absolute;
    left: 0; right: 0;
    top: 108px;
    display: flex;
    align-items: center;
    justify-content: center;
    gap: 14px;
  }
  .wordmark__square {
    width: 22px; height: 22px;
    background: var(--accent);
  }
  .wordmark__name {
    color: var(--white);
    font-size: 44px;
    font-weight: 500;
    letter-spacing: 1px;
    line-height: 1;
  }
  .brand-row {
    position: absolute;
    left: 0; right: 0;
    top: 245px;
    display: flex;
    justify-content: center;
    gap: 18px;
    list-style: none;
  }
  .brand-row__item {
    color: var(--muted);
    font-size: 12px;
    font-weight: 500;
    letter-spacing: 0.5px;
  }

  /* Back */
  .holder {
    position: absolute;
    right: 265px;
    top: 148px;
    text-align: right;
  }
  .holder__name {
    font-size: 17px;
    font-weight: 600;
    color: var(--ink);
    line-height: 1.1;
  }
  .holder__role {
    font-size: 11.5px;
    color: var(--ink);
    margin-top: 4px;
  }
  .divider {
    position: absolute;
    left: 235px;
    top: 103px;
    width: 2px;
    height: 124px;
    background: linear-gradient(to bottom, transparent, var(--accent) 30%, var(--accent) 70%, transparent);
  }
  .contact {
    position: absolute;
    left: 268px;
    top: 118px;
    list-style: none;
  }
  .contact__row {
    display: flex;
    align-items: center;
    gap: 6px;
    height: 24px;
    font-size: 11.5px;
    color: var(--ink);
  }
  .contact__icon { width: 12px; height: 12px; fill: var(--accent); flex: none; }
  .address {
    position: absolute;
    left: 270px;
    top: 198px;
    font-style: normal;
    font-size: 13px;
    font-weight: 600;
    line-height: 17px;
    color: var(--ink);
  }
</style>
</head>
<body>
  <section class="card card--front">
    <div class="facet-texture" role="img" aria-label="Dark faceted low-poly background texture"></div>
    <div class="wordmark">
      <span class="wordmark__square"></span>
      <span class="wordmark__name">Fen Athletics</span>
    </div>
    <ul class="brand-row">
      <li class="brand-row__item">TavaPuni</li>
      <li class="brand-row__item">Grit and Rain</li>
      <li class="brand-row__item">ElmStretch</li>
      <li class="brand-row__item">Fen</li>
    </ul>
  </section>

  <section class="card card--back">
    <div class="facet-texture" role="img" aria-label="White faceted low-poly background texture"></div>
    <div class="holder">
      <p class="holder__name">Colin Ashby</p>
      <p class="holder__role">Managing Director</p>
    </div>
    <div class="divider"></div>
    <ul class="contact">
      <li class="contact__row">
        <svg class="contact__icon" viewBox="0 0 12 12" aria-hidden="true"><path d="M1 3.5C1 2 3 1.5 6 1.5S11 2 11 3.5V5H8.5V4h-5v1H1z"/><rect x="2" y="6" width="8" height="5" rx="1"/></svg>
        <span>+44 (0)1632 960418</span>
      </li>
      <li class="contact__row">
        <svg class="contact__icon" viewBox="0 0 12 12" aria-hidden="true"><rect x="3" y="1" width="6" height="3"/><rect x="1" y="4.5" width="10" height="4.5" rx="1"/><rect x="3" y="7.5" width="6" height="3.5"/></svg>
        <span>(713) 555-0147</span>
      </li>
      <li class="contact__row">
        <svg class="contact__icon" viewBox="0 0 12 12" aria-hidden="true"><path d="M1 2.5h10v7H1z M1.6 3l4.4 3.5L10.4 3" stroke="#fff" stroke-width="0.8"/></svg>
        <span>colin@fenathletics.co.uk</span>
      </li>
    </ul>
    <address class="address">Reed Park, Aldwick<br>Ripley, HG3 9ZZ</address>
  </section>
</body>
</html>
```